Healthy lifestyle Influencer business card

I need your creativity to have a business card that I can leave in all the restaurants, hotels and spas I visit to inform them that I am an influencer specializing in the wellness sector and that I will write a review about them. You can use my instagram photos Lunavita27 or on my website www.piattileggeriorto.it. I would like my business card to impress with its creativity! thank you very much!

Contact Information for Business Card

siteweb, instagram, phone number

Font styles to use
Decorative
Script

Colors
0094D4
00A9DD
6FCCEA
C7EBF8
E9F6FB
59FF00
82FF00
B8FF75
E3FFCB
F4FFEA
FFC000
F8CF3A
FAE287
FDF2CF
FEFAEE
F0912C
F2A743
F7CA91
FBE8D2
FDF5EE
EE7325
F08F49
F5BC92
FAE3D3
FDF4ED
EB3D1F
EC4F4E
F09395
F8D3D4
FCEDEE
E54698
E96AAD
F1A4CE
F9D9EA
FCEFF6

Requirements
Nice to have
• creativity

```html
<!DOCTYPE html>
<html lang="it">
<head>
<meta charset="utf-8">
<title>Cucina Lunare – Biglietto da visita</title>
<link href="https://fonts.googleapis.com/css2?family=Great+Vibes&family=Roboto:wght@300;400&display=swap" rel="stylesheet">
<style>
  :root {
    --backdrop: #3a3a3b;
    --card-dark: #1f2022;
    --card-dark-2: #2a2b2d;
    --ink-light: #e8e8e8;
    --ink-muted: #b9bbbd;
    --ink-logo: #8d8f92;
    --band-grey: #4b4c4e;
    --panel-teal: #97bbb1;
    --panel-ink: #5d6664;
    --dot: #9aa0a3;
  }
  * { margin: 0; padding: 0; box-sizing: border-box; }
  html, body { width: 1200px; height: 1138px; overflow: hidden; }
  body {
    background: var(--backdrop);
    font-family: "Roboto", Arial, sans-serif;
    position: relative;
  }
  .card {
    position: absolute;
    width: 622px;
    height: 376px;
    border-radius: 16px;
    overflow: hidden;
    background: linear-gradient(160deg, var(--card-dark-2), var(--card-dark) 60%);
  }
  .card--front { left: 272px; top: 184px; }
  .card--back { left: 274px; top: 606px; }

  .brand-name {
    position: absolute;
    left: 0; right: 0;
    text-align: center;
    font-weight: 300;
    color: var(--ink-logo);
  }
  .card--front .brand-name { top: 146px; font-size: 52px; letter-spacing: 1px; }
  .tagline {
    position: absolute;
    left: 0; right: 0;
    text-align: center;
    font-weight: 400;
    color: var(--ink-logo);
  }
  .card--front .tagline { top: 224px; font-size: 21px; }

  .social {
    position: absolute;
    display: flex;
    align-items: center;
    gap: 10px;
    color: var(--ink-light);
    font-weight: 400;
  }
  .social__dot { width: 15px; height: 15px; border-radius: 50%; background: var(--dot); }
  .card--front .social { left: 0; right: 0; justify-content: center; top: 333px; font-size: 17px; }

  .holder-name {
    position: absolute;
    left: 34px; top: 46px;
    font-family: "Great Vibes", cursive;
    font-weight: 400;
    font-size: 44px;
    color: var(--ink-light);
  }
  .contact {
    position: absolute;
    left: 34px; top: 216px;
    list-style: none;
    font-size: 14.5px;
    font-weight: 300;
    color: var(--ink-light);
  }
  .contact li { display: flex; align-items: center; gap: 9px; height: 21px; }
  .contact svg { width: 13px; height: 13px; fill: none; stroke: var(--ink-muted); stroke-width: 1.4; }
  .vat {
    position: absolute;
    left: 34px; top: 284px;
    font-size: 14.5px; font-weight: 300;
    color: var(--ink-muted);
  }
  .card--back .social { left: 34px; top: 322px; font-size: 17px; font-weight: 300; }

  .panel { position: absolute; inset: 0; width: 622px; height: 376px; }
  .panel-logo {
    position: absolute;
    left: 512px; top: 188px;
    width: 290px;
    transform: translate(-50%, -50%) rotate(90deg);
    text-align: center;
    color: var(--panel-ink);
  }
  .panel-logo .panel-name { font-weight: 300; font-size: 38px; line-height: 1.1; }
  .panel-logo .panel-tagline { font-size: 14px; margin-top: 4px; }
</style>
</head>
<body>

<section class="card card--front" aria-label="Fronte del biglietto">
  <p class="brand-name">Cucina Lunare</p>
  <p class="tagline">Benessere a tavola, ogni giorno</p>
  <p class="social"><span class="social__dot"></span>@Lunavita27</p>
</section>

<section class="card card--back" aria-label="Retro del biglietto">
  <svg class="panel" viewBox="0 0 622 376" aria-hidden="true">
    <path d="M430 0 Q322 188 454 376 L622 376 L622 0 Z" fill="var(--band-grey)"/>
    <path d="M458 0 Q324 188 454 376 L622 376 L622 0 Z" fill="var(--panel-teal)"/>
  </svg>

  <h1 class="holder-name">Luna Ferretti</h1>

  <ul class="contact">
    <li>
      <svg viewBox="0 0 14 14"><path d="M3 2 L5 2 L6 5 L4.5 6 Q5.5 8.5 8 9.5 L9 8 L12 9 L12 11 Q7 12 3.5 8 Q1.5 5 3 2 Z"/></svg>
      000-0000-0000
    </li>
    <li>
      <svg viewBox="0 0 14 14"><rect x="1.5" y="3" width="11" height="8"/><path d="M1.5 3 L7 7.5 L12.5 3"/></svg>
      info@piattileggeriorto.it
    </li>
    <li>
      <svg viewBox="0 0 14 14"><circle cx="7" cy="7" r="5.5"/><ellipse cx="7" cy="7" rx="2.3" ry="5.5"/><path d="M1.5 7 H12.5"/></svg>
      www.piattileggeriorto.it
    </li>
  </ul>
  <p class="vat">Partita IVA 01234560789</p>
  <p class="social"><span class="social__dot"></span>@Lunavita27</p>

  <div class="panel-logo">
    <p class="panel-name">Cucina Lunare</p>
    <p class="panel-tagline">Benessere a tavola, ogni giorno</p>
  </div>
</section>

</body>
</html>
```